Mindfulness School for Children -- Business Cards

We're looking for business cards for our school directors and owners. We're a mindfulness school for children called little lanterns. Attached are our logos/icons.

```html
<!DOCTYPE html>
<html lang="en">
<head>
<meta charset="utf-8">
<title>little lanterns — business card</title>
<link href="https://fonts.googleapis.com/css2?family=Karla:wght@400;500;700&display=swap" rel="stylesheet">
<style>
  :root {
    --backdrop: #2a2b2e;
    --card-white: #ffffff;
    --teal-light: #3fd3ea;
    --teal-mid: #2aa6bd;
    --teal-deep: #0f6f93;
    --brand-teal: #3a9fb5;
    --brand-soft: #7cc4d2;
    --ink: #4a4a4a;
    --icon: #4ea98f;
  }
  * { box-sizing: border-box; margin: 0; padding: 0; }
  html, body {
    width: 1200px; height: 874px; overflow: hidden;
    background: var(--backdrop);
    font-family: "Karla", Arial, sans-serif;
  }
  .canvas {
    position: relative; width: 1200px; height: 874px;
  }
  .card {
    position: absolute; left: 270px; width: 660px; height: 377px;
    border-radius: 3px; overflow: hidden;
    box-shadow: 0 10px 26px rgba(0,0,0,.45);
  }
  .card--back { top: 50px; }
  .card--front { top: 447px; background: var(--card-white); }

  .back-pattern {
    position: absolute; inset: 0;
    background: linear-gradient(115deg, var(--teal-light) 0%, var(--teal-mid) 45%, var(--teal-deep) 100%);
  }
  .back-mark {
    position: absolute; right: 96px; bottom: 52px;
    width: 54px; height: 54px; border-radius: 50%;
    background: rgba(255,255,255,.55);
  }

  .brand {
    position: absolute; left: 38px; top: 36px;
    display: flex; align-items: center; gap: 10px;
  }
  .brand__name {
    font-size: 34px; font-weight: 500; color: var(--brand-teal);
    letter-spacing: .3px;
  }
  .brand__dot {
    width: 14px; height: 14px; border-radius: 50%; background: var(--brand-teal);
  }

  .person { position: absolute; left: 38px; top: 108px; }
  .person__name {
    font-size: 21px; font-weight: 700; color: var(--brand-teal);
    letter-spacing: 1px; text-transform: uppercase;
  }
  .person__role { font-size: 14px; color: var(--brand-soft); margin-top: 1px; }

  .address {
    position: absolute; left: 38px; top: 175px;
    font-size: 14.5px; line-height: 19px; color: var(--ink);
  }
  .contacts {
    position: absolute; left: 38px; top: 228px; list-style: none;
    font-size: 14.5px; line-height: 20px; color: var(--ink);
  }
  .contacts li { display: flex; align-items: center; gap: 9px; }
  .contacts svg { width: 12px; height: 12px; fill: var(--icon); flex: none; }

  .front-mark {
    position: absolute; right: 40px; top: 78px;
    width: 300px; height: 260px; border-radius: 48% 48% 40% 40%;
    background: radial-gradient(circle at 50% 45%, #8fcbd8 0%, #5eb3c6 70%, #4ea8bd 100%);
    opacity: .85;
  }
</style>
</head>
<body>
<main class="canvas">
  <section class="card card--back">
    <div class="back-pattern" role="img" aria-label="Repeating embossed flower pattern in glossy teal"></div>
    <div class="back-mark" role="img" aria-label="Small white brand mark"></div>
  </section>

  <section class="card card--front">
    <div class="brand">
      <span class="brand__name">little lanterns</span>
      <span class="brand__dot"></span>
    </div>

    <div class="person">
      <p class="person__name">Daniel Reyes</p>
      <p class="person__role">President</p>
    </div>

    <address class="address" style="font-style:normal">
      2140 Willow Crest Road<br>
      Juneau, Alaska 99801
    </address>

    <ul class="contacts">
      <li>
        <svg viewBox="0 0 24 24" aria-hidden="true"><path d="M6.6 10.8a15.1 15.1 0 0 0 6.6 6.6l2.2-2.2a1 1 0 0 1 1-.25 11.4 11.4 0 0 0 3.6.57 1 1 0 0 1 1 1V20a1 1 0 0 1-1 1A17 17 0 0 1 3 4a1 1 0 0 1 1-1h3.5a1 1 0 0 1 1 1c0 1.25.2 2.45.57 3.57a1 1 0 0 1-.25 1z"/></svg>
        555-214-7730
      </li>
      <li>
        <svg viewBox="0 0 24 24" aria-hidden="true"><path d="M7 1h10a2 2 0 0 1 2 2v18a2 2 0 0 1-2 2H7a2 2 0 0 1-2-2V3a2 2 0 0 1 2-2zm0 3v14h10V4zm5 15.5a1 1 0 1 0 0 2 1 1 0 0 0 0-2z"/></svg>
        555-618-2094
      </li>
      <li>
        <svg viewBox="0 0 24 24" aria-hidden="true"><path d="M6 2h12v6H6zM4 9h16a2 2 0 0 1 2 2v7h-4v4H6v-4H2v-7a2 2 0 0 1 2-2zm4 8v3h8v-3z"/></svg>
        555-347-5162
      </li>
      <li>
        <svg viewBox="0 0 24 24" aria-hidden="true"><path d="M2 5h20v14H2zm2 2v.5l8 5 8-5V7z"/></svg>
        name@littlelanterns.com
      </li>
      <li>
        <svg viewBox="0 0 24 24" aria-hidden="true"><circle cx="12" cy="12" r="10"/></svg>
        www.littlelanterns.com
      </li>
    </ul>

    <div class="front-mark" role="img" aria-label="Large soft watercolour brand mark in teal"></div>
  </section>
</main>
</body>
</html>
```